Business Card Design Project

I need a business card designed from scratch. I have an existing logo that I can upload in Illustrator for modification or redesign.

The Company is called Query Lanterns http://querylanterns.com.au and we provide Search Engine Optimization services to Australian businesses. The current logo signifies an increase in visitors, profits etc...

There are no restrictions as to the redesign - colours, style etc are all open to change.

Cards will be full colour and one sided printed at http://www.cardmoxel.com.au so check their requirements for file format and sizes etc.

I will expect all original files upon completion of project.

Target Market(s)

Any business with a web site looking to improve their search engine rankings

Industry/Entity Type

Business

Requirements
Must have
• I like modern, sleek designs. Clean, not fussy, uncluttered.

```html
<!DOCTYPE html>
<html lang="en">
<head>
<meta charset="utf-8">
<title>Query Lanterns – Business Card</title>
<link rel="stylesheet" href="https://fonts.googleapis.com/css2?family=Source+Sans+3:wght@400;600;700&display=swap">
<style>
  :root {
    --backdrop: #a87c26;
    --card: #ffffff;
    --brand-blue: #1a6fb3;
    --deep-blue: #1c3f73;
    --mid-blue: #3b86c6;
    --sun-yellow: #f2c21b;
    --sun-orange: #f7931e;
    --ink: #2b2b2b;
    --rule: #9a9a9a;
  }
  * { margin: 0; padding: 0; box-sizing: border-box; }
  html, body { width: 1200px; height: 686px; overflow: hidden; }
  body {
    background: var(--backdrop);
    font-family: "Source Sans 3", "Myriad Pro", Arial, sans-serif;
    position: relative;
  }
  .card {
    position: absolute;
    width: 494px;
    height: 281px;
    background: var(--card);
    border-radius: 19px;
    overflow: hidden;
    box-shadow: 1px 2px 2px rgba(0,0,0,0.55);
  }
  .card--front { left: 81px; top: 139px; }
  .card--back { left: 617px; top: 267px; }

  .side-band { position: absolute; right: 0; top: 0; width: 35px; height: 100%; }

  .brand {
    position: absolute;
    left: 0; right: 35px;
    top: 66px;
    display: flex;
    align-items: center;
    justify-content: center;
    gap: 10px;
    color: var(--brand-blue);
    font-weight: 700;
    font-size: 38px;
    letter-spacing: -0.5px;
    line-height: 1;
  }
  .brand__dot {
    width: 22px; height: 22px;
    border-radius: 50%;
    background: var(--sun-yellow);
    flex: none;
  }

  .identity {
    position: absolute;
    right: calc(494px - 176px);
    top: 162px;
    text-align: right;
    color: var(--ink);
    font-size: 12.5px;
    line-height: 16px;
  }
  .identity__headline { display: flex; align-items: baseline; justify-content: flex-end; margin-bottom: 6px; }
  .identity__name { color: var(--brand-blue); font-weight: 600; font-size: 18px; line-height: 20px; }
  .identity__title {
    color: var(--sun-yellow); font-weight: 700; font-size: 12.5px;
    border-left: 1px solid var(--rule); margin-left: 7px; padding-left: 7px;
  }

  .divider {
    position: absolute; left: 192px; top: 158px; width: 1px; height: 76px;
    background: linear-gradient(to bottom, rgba(150,150,150,0), var(--rule) 25%, var(--rule) 75%, rgba(150,150,150,0));
  }

  .contact {
    position: absolute; left: 206px; top: 167px;
    list-style: none; color: var(--ink); font-size: 12.5px;
  }
  .contact__item { display: flex; align-items: center; gap: 4px; height: 19px; }
  .contact__icon { width: 11px; height: 11px; flex: none; }

  .back-brand {
    position: absolute; inset: 0;
    display: flex; align-items: center; justify-content: center; gap: 12px;
    color: var(--brand-blue); font-weight: 700; font-size: 40px; letter-spacing: -0.5px;
  }
</style>
</head>
<body>

<section class="card card--front" aria-label="Business card front">
  <svg class="side-band" viewBox="0 0 35 281" preserveAspectRatio="none" aria-hidden="true">
    <defs>
      <linearGradient id="band-warm" x1="0" y1="0" x2="0" y2="1">
        <stop offset="0" stop-color="#f7941d"/>
        <stop offset="1" stop-color="#f5dd2a"/>
      </linearGradient>
      <linearGradient id="band-cool" x1="0" y1="0" x2="0" y2="1">
        <stop offset="0" stop-color="#4a9ad6"/>
        <stop offset="1" stop-color="#1b3a6b"/>
      </linearGradient>
    </defs>
    <rect x="0" y="0" width="35" height="281" fill="url(#band-cool)"/>
    <polygon points="0,0 35,0 35,90 0,114" fill="url(#band-warm)"/>
  </svg>

  <div class="brand">
    <span class="brand__dot"></span>
    <span class="brand__name">Query Lanterns</span>
  </div>

  <div class="identity">
    <div class="identity__headline">
      <span class="identity__name">Your Name</span>
      <span class="identity__title">Title</span>
    </div>
    <p>Street name City</p>
    <p>State, zip code</p>
  </div>

  <div class="divider"></div>

  <ul class="contact">
    <li class="contact__item">
      <svg class="contact__icon" viewBox="0 0 12 12" aria-hidden="true">
        <path d="M2.5 1 L4.5 1 L5 3.5 L3.8 4.5 C4.5 6 5.8 7.4 7.3 8.2 L8.4 7 L11 7.6 L11 9.6 C11 10.4 10.3 11 9.5 11 C5 10.6 1.4 7 1 2.5 C1 1.6 1.6 1 2.5 1 Z" fill="var(--brand-blue)"/>
      </svg>
      <span>123-456-7890</span>
    </li>
    <li class="contact__item">
      <svg class="contact__icon" viewBox="0 0 12 12" aria-hidden="true">
        <rect x="0.5" y="2.5" width="11" height="7.5" fill="var(--brand-blue)"/>
        <path d="M0.5 2.5 L6 7 L11.5 2.5" fill="none" stroke="#fff" stroke-width="1"/>
      </svg>
      <span>inquiry@querylanterns.com.au.com</span>
    </li>
    <li class="contact__item">
      <svg class="contact__icon" viewBox="0 0 12 12" aria-hidden="true">
        <circle cx="6" cy="6" r="5.2" fill="var(--brand-blue)"/>
        <g fill="none" stroke="#fff" stroke-width="0.8">
          <ellipse cx="6" cy="6" rx="2.2" ry="5.2"/>
          <line x1="0.8" y1="6" x2="11.2" y2="6"/>
          <line x1="1.6" y1="3.5" x2="10.4" y2="3.5"/>
          <line x1="1.6" y1="8.5" x2="10.4" y2="8.5"/>
        </g>
      </svg>
      <span>www.querylanterns.com.au</span>
    </li>
  </ul>
</section>

<section class="card card--back" aria-label="Business card back">
  <div class="back-brand">
    <span class="brand__dot"></span>
    <span>Query Lanterns</span>
  </div>
</section>

</body>
</html>
```